HearthMile business card and stationary design

We are looking for a simple yet elegant design for our mortgage company business card and stationary.

The card should include:
Name (Marcus Pell)
Title (CEO)
Phone Number (732-555-0182)
Address (48 Birchwell Court, Suite 314, Hazlet, NJ 07730)
Email (email@hearthmile.example)
"NMLS" i.e. (NMLS 61947)
"Company NMLS" (Company NMLS 274615)

Contact Information for Business Card

See above

```html
<!DOCTYPE html>
<html lang="en">
<head>
<meta charset="utf-8">
<title>HearthMile Business Card</title>
<link href="https://fonts.googleapis.com/css2?family=Montserrat:wght@400;500;600;700&display=swap" rel="stylesheet">
<style>
  :root {
    --stage: #2e2f31;
    --paper: #ffffff;
    --navy: #16222f;
    --deep: #19283a;
    --sky: #0aa5e6;
    --ocean: #0b8cc4;
    --ink: #1b1d20;
    --rule: #cfd3d7;
  }
  * { margin: 0; padding: 0; box-sizing: border-box; }
  html, body { width: 1200px; height: 866px; overflow: hidden; }
  body {
    background: var(--stage);
    font-family: "Montserrat", sans-serif;
    display: flex;
    flex-direction: column;
    align-items: center;
    justify-content: center;
    gap: 44px;
  }
  .card {
    width: 660px;
    height: 378px;
    position: relative;
    overflow: hidden;
    box-shadow: 0 10px 28px rgba(0,0,0,.45);
  }
  .card-front { background: var(--paper); color: var(--ink); }
  .identity { position: absolute; left: 46px; top: 44px; }
  .person-name { font-size: 28px; font-weight: 700; color: var(--navy); letter-spacing: .2px; line-height: 34px; }
  .person-name .surname { color: var(--sky); }
  .person-title { font-size: 17px; font-weight: 500; color: var(--navy); line-height: 20px; }
  .contacts { list-style: none; margin-top: 14px; font-size: 14px; font-weight: 500; }
  .contacts li { display: flex; align-items: center; gap: 9px; line-height: 22px; }
  .contacts svg { width: 14px; height: 14px; fill: var(--sky); flex: none; }
  .contacts .accent { color: var(--sky); }
  .rule-top { position: absolute; left: 232px; right: 36px; top: 62px; height: 1px; background: var(--rule); }
  .wordmark {
    position: absolute;
    right: 48px;
    top: 180px;
    font-size: 50px;
    line-height: 60px;
    font-weight: 600;
    color: var(--navy);
    letter-spacing: 1px;
  }
  .rule-bottom { position: absolute; left: 300px; right: 36px; top: 256px; height: 1px; background: var(--rule); }
  .licensing {
    position: absolute;
    right: 46px;
    top: 266px;
    text-align: right;
    font-size: 14px;
    font-weight: 500;
    line-height: 21px;
  }
  .licensing .accent { color: var(--sky); }
  .card-back {
    background: linear-gradient(120deg, var(--navy) 0%, var(--deep) 38%, #124a6b 68%, var(--ocean) 100%);
    display: flex;
    align-items: center;
    justify-content: center;
  }
  .card-back .wordmark-reverse {
    font-size: 62px;
    font-weight: 600;
    color: var(--paper);
    letter-spacing: 1px;
  }
</style>
</head>
<body>
  <section class="card card-front" aria-label="Business card front">
    <div class="identity">
      <h1 class="person-name">Marcus <span class="surname">Pell</span></h1>
      <p class="person-title">CEO</p>
      <ul class="contacts">
        <li><svg viewBox="0 0 24 24" aria-hidden="true"><path d="M6.6 10.8a15 15 0 0 0 6.6 6.6l2.2-2.2c.3-.3.7-.4 1-.2 1.1.4 2.3.6 3.6.6.6 0 1 .4 1 1V20c0 .6-.4 1-1 1A17 17 0 0 1 3 4c0-.6.4-1 1-1h3.5c.6 0 1 .4 1 1 0 1.3.2 2.5.6 3.6.1.3 0 .7-.2 1z"/></svg><span>732-555-0182</span></li>
        <li><svg viewBox="0 0 24 24" aria-hidden="true"><path d="M2 5h20v14H2z M2 5l10 8 10-8" stroke="#fff" stroke-width="1.5"/></svg><span>email@hearthmile.example</span></li>
        <li><svg viewBox="0 0 24 24" aria-hidden="true"><circle cx="12" cy="12" r="10"/><path d="M2 12h20M12 2c3 3 3 17 0 20M12 2c-3 3-3 17 0 20" stroke="#fff" stroke-width="1.4" fill="none"/></svg><span>www.<span class="accent">hearthmile</span>.example</span></li>
      </ul>
    </div>
    <div class="rule-top"></div>
    <div class="wordmark">HearthMile</div>
    <div class="rule-bottom"></div>
    <div class="licensing">
      <p><span class="accent">NMLS</span> 61947</p>
      <p><span class="accent">Company NMLS</span> 274615</p>
      <p>48 Birchwell Court, Suite 314</p>
      <p>Alder Bay, NJ 07799</p>
    </div>
  </section>

  <section class="card card-back" aria-label="Business card back">
    <div class="wordmark-reverse">HearthMile</div>
  </section>
</body>
</html>
```